Need A Standard Musical Download Website

We are looking for a talented designer to create a unique web design for our startup Music website called Vorde Sound.
The website should be responsive and filled with some creative stuffs along with bright colors.

Vorde sound is a website loaded with different types of music and capable of downloading the requested music by its users.
There will be categories of music which would be sorted by the genre. They include RnB, Hip-Hop, Afro pop, Pop, Dancehall and Reggae).

DESIGN STYLE/THEME

Creative, trendy, colorful, unique, and easy to use. You have freedom of selecting which ever color suits you. The design must be energetic and attractive.

NAVIGATION

HOME-MUSIC(RnB, Hip hop, Afro pop, POP, dancehall, Reggae)-ARTISTE-NEWS-LOGIN

PAGES REQUIRED
------------
1)Home Page
2)Music

FONTS
GOOGLE FONTS is strongly recommended.

Designers can get inspiration from https://tunabrook.example

Industry/Entity Type

Startup

```html
<!DOCTYPE html>
<html lang="en">
<head>
<meta charset="utf-8">
<title>Vorde Sound</title>
<link href="https://fonts.googleapis.com/css2?family=Montserrat:wght@500;700&family=Roboto:wght@400;500&family=Oswald:wght@400&family=Open+Sans:wght@400;600&family=Catamaran:wght@500;600;700&display=swap" rel="stylesheet">
<style>
:root{
  --red:#ee2722;
  --coral:#fe5e55;
  --ink:#2b2b2b;
  --muted:#555;
  --white:#fff;
  --footer:#f1f1f1;
  --hero-a:#4a5a3a;
  --hero-b:#6f7f9c;
}
*{box-sizing:border-box;margin:0;padding:0}
html,body{width:1195px;height:1200px;overflow:hidden;background:var(--white)}
body{position:relative;font-family:"Open Sans",sans-serif;color:var(--ink)}

/* header */
.site-header{position:absolute;left:0;top:0;width:1195px;height:106px;background:var(--white)}
.brand{display:flex;align-items:center;gap:10px;font-family:"Montserrat",sans-serif;font-weight:500;color:var(--ink)}
.brand-dot{width:30px;height:30px;border-radius:50%;background:var(--red)}
.site-header .brand{position:absolute;left:97px;top:36px;font-size:29px}
.main-nav a{position:absolute;top:0;height:106px;line-height:108px;font-family:"Roboto",sans-serif;font-size:16px;color:var(--ink);text-decoration:none}
.main-nav a.active{background:var(--red);color:var(--white);width:86px;text-align:center;left:433px;font-weight:500}
.caret{display:inline-block;width:0;height:0;border-left:5px solid transparent;border-right:5px solid transparent;border-top:5px solid var(--ink);margin-left:8px;vertical-align:middle}
.social{position:absolute;border:2px solid var(--ink);border-radius:50%}
.header-social .social{width:33px;height:33px;top:38px}

/* hero */
.hero{position:absolute;left:0;top:106px;width:796px;height:534px;background:linear-gradient(120deg,var(--hero-a) 0%,#55603f 45%,var(--hero-b) 100%)}
.hero-title{position:absolute;left:97px;top:118px;font-family:"Montserrat",sans-serif;font-weight:700;font-size:60px;color:var(--white);letter-spacing:1px}
.hero-sub{position:absolute;left:96px;top:206px;font-family:"Roboto",sans-serif;font-weight:500;font-size:22px;color:var(--white)}
.play-now{position:absolute;left:98px;top:314px;width:180px;height:56px;border:2px solid var(--white);background:rgba(255,255,255,.3);font-family:"Oswald",sans-serif;font-size:28px;color:var(--white);padding-left:24px;line-height:52px}
.free-badge{position:absolute;left:250px;top:290px;width:104px;height:104px;border-radius:50%;background:var(--red);border:2px solid var(--white);color:var(--white);text-align:center;font-family:"Catamaran",sans-serif;font-weight:600}
.free-badge b{display:block;font-size:24px;margin-top:22px;line-height:1}
.free-badge span{display:block;font-size:17px;margin-top:6px}

/* trial form */
.trial{position:absolute;left:796px;top:106px;width:399px;height:534px;background:var(--coral)}
.trial::before{content:"";position:absolute;inset:4px;border:2px solid var(--white)}
.trial h2{position:absolute;left:0;width:399px;top:40px;text-align:center;font-family:"Catamaran",sans-serif;font-weight:700;font-size:24px;color:var(--white)}
.trial .rule{position:absolute;left:147px;top:88px;width:105px;height:2px;background:var(--white)}
.field{position:absolute;left:30px;width:338px;height:48px;border:2px solid var(--white);border-radius:3px;font-family:"Catamaran",sans-serif;font-weight:600;font-size:15px;color:var(--white);padding-left:10px;line-height:46px}
.field svg{position:absolute;right:10px;top:16px}
.check{position:absolute;left:30px;top:369px;font-family:"Catamaran",sans-serif;font-weight:500;font-size:15px;color:var(--white);display:flex;align-items:center;gap:9px}
.check i{width:14px;height:14px;background:var(--white);border-radius:3px;display:block}
.trial-btn{position:absolute;left:30px;top:411px;width:244px;height:49px;background:var(--white);border-radius:3px;font-family:"Catamaran",sans-serif;font-weight:600;font-size:16px;color:var(--red);line-height:50px;padding-left:23px}
.trial-btn svg{vertical-align:-2px;margin-left:6px}
.terms{position:absolute;left:29px;top:476px;font-family:"Catamaran",sans-serif;font-weight:500;font-size:15px;color:var(--white)}

/* features */
.features{position:absolute;left:0;top:640px;width:1195px;height:200px}
.feature{position:absolute;top:0;height:200px;background:linear-gradient(#f6f6f6,var(--white) 30%,var(--white) 75%,#f3f3f3)}
.feature.alt{background:linear-gradient(90deg,#e4e4e4,#f7f7f7 12%,#f7f7f7 88%,#e4e4e4)}
.feature .icon{position:absolute;left:23px;top:57px;width:86px;height:86px;border-radius:50%;border:3px solid var(--ink);display:flex;align-items:center;justify-content:center;background:var(--white)}
.feature.alt .icon{background:var(--red);border:4px solid var(--white);box-shadow:0 0 0 1px #ddd}
.feature h3{position:absolute;left:125px;top:59px;font-family:"Catamaran",sans-serif;font-weight:500;font-size:18px;color:var(--ink)}
.feature p{position:absolute;left:126px;top:92px;width:265px;font-size:12.5px;line-height:20px;color:var(--muted);letter-spacing:.2px}

/* footer */
.site-footer{position:absolute;left:0;top:843px;width:1195px;height:357px;background:var(--footer);border-top:3px solid var(--red)}
.site-footer .brand{position:absolute;left:0;width:1195px;justify-content:center;top:62px;font-size:30px}
.contact-row{position:absolute;left:0;top:154px;width:1195px;display:flex;justify-content:center;gap:30px}
.contact{display:flex;align-items:center;gap:10px;font-size:18px;color:var(--ink);white-space:nowrap}
.contact .ring{flex:none;width:36px;height:36px;border:2px solid var(--ink);border-radius:50%;display:flex;align-items:center;justify-content:center}
.footer-nav{position:absolute;left:0;width:1195px;top:228px;display:flex;justify-content:center;gap:24px;font-family:"Roboto",sans-serif;font-weight:500;font-size:14px;color:var(--ink)}
.footer-rule{position:absolute;left:97px;top:282px;width:999px;height:2px;background:var(--ink)}
.copyright{position:absolute;left:97px;top:311px;font-size:14px;color:var(--ink)}
.footer-social .social{width:32px;height:32px;top:307px}
</style>
</head>
<body>

<header class="site-header">
  <div class="brand"><span class="brand-dot"></span>Vorde Sound</div>
  <nav class="main-nav">
    <a class="active" href="#">HOME</a>
    <a href="#" style="left:546px">MUSIC<span class="caret"></span></a>
    <a href="#" style="left:640px">ARTISTE</a>
    <a href="#" style="left:746px">NEWS</a>
    <a href="#" style="left:837px">LOGIN</a>
  </nav>
  <div class="header-social" aria-label="Social links">
    <span class="social" style="left:907px"></span>
    <span class="social" style="left:946px"></span>
    <span class="social" style="left:986px"></span>
    <span class="social" style="left:1025px"></span>
    <span class="social" style="left:1063px"></span>
  </div>
</header>

<section class="hero" role="img" aria-label="Photo of a young woman lying on grass and daisies, listening to music on headphones">
  <h1 class="hero-title">VORDE SOUND</h1>
  <p class="hero-sub">Vorde sound is a website loaded with different types of music</p>
  <div class="play-now">PLAY NOW</div>
  <div class="free-badge"><b>FREE</b><span>TRIAL!</span></div>
</section>

<aside class="trial">
  <h2>START YOUR TRIAL</h2>
  <div class="rule"></div>
  <div class="field" style="top:122px">Email Address</div>
  <div class="field" style="top:182px">Password
    <svg width="10" height="13" viewBox="0 0 10 13"><rect x="0" y="5" width="10" height="8" rx="1" fill="#fff"/><path d="M2.5 5V3.5a2.5 2.5 0 0 1 5 0V5" stroke="#fff" stroke-width="1.6" fill="none"/></svg></div>
  <div class="field" style="top:242px">Re-Enter Password
    <svg width="10" height="13" viewBox="0 0 10 13"><rect x="0" y="5" width="10" height="8" rx="1" fill="#fff"/><path d="M2.5 5V3.5a2.5 2.5 0 0 1 5 0V5" stroke="#fff" stroke-width="1.6" fill="none"/></svg></div>
  <div class="field" style="top:301px">Country
    <svg width="10" height="6" viewBox="0 0 10 6" style="top:25px"><path d="M0 0h10L5 6z" fill="#fff"/></svg></div>
  <div class="check"><i></i>Email me about new &amp; free music</div>
  <div class="trial-btn">START YOUR FREE TRIAL<svg width="14" height="13" viewBox="0 0 14 13"><path d="M0 5h8V1l6 5.5L8 12V8H0z" fill="#ee2722"/></svg></div>
  <div class="terms">Terms and Conditions</div>
</aside>

<section class="features">
  <div class="feature" style="left:0;width:400px">
    <div class="icon"><svg width="48" height="48" viewBox="0 0 48 48"><circle cx="22" cy="26" r="15" fill="none" stroke="#2b2b2b" stroke-width="5"/><circle cx="22" cy="26" r="4" fill="#2b2b2b"/><path d="M34 12c6 6 6 18 0 26" stroke="#2b2b2b" stroke-width="5" fill="none"/></svg></div>
    <h3>Unlimited Personal Download</h3>
    <p>There will be categories of music which would be sorted by the genre. They include RnB, Hip-Hop.</p>
  </div>
  <div class="feature alt" style="left:400px;width:396px">
    <div class="icon"><svg width="56" height="56" viewBox="0 0 56 56"><circle cx="28" cy="28" r="16" fill="none" stroke="#fff" stroke-width="3"/><circle cx="28" cy="28" r="9" fill="none" stroke="#fff" stroke-width="3"/><circle cx="28" cy="28" r="3.5" fill="#fff"/><path d="M8 20c-3 5-3 11 0 16M4 17c-4 7-4 15 0 22M48 20c3 5 3 11 0 16M52 17c4 7 4 15 0 22" stroke="#fff" stroke-width="2" fill="none"/></svg></div>
    <h3>Types Of Music</h3>
    <p>There will be categories of music which would be sorted by the genre. They include RnB, Hip-Hop.</p>
  </div>
  <div class="feature" style="left:796px;width:399px">
    <div class="icon"><svg width="44" height="44" viewBox="0 0 44 44"><rect x="4" y="4" width="36" height="36" rx="6" fill="none" stroke="#2b2b2b" stroke-width="4"/><circle cx="24" cy="20" r="9" fill="none" stroke="#2b2b2b" stroke-width="4"/><circle cx="24" cy="20" r="2.5" fill="#2b2b2b"/><path d="M12 34l6-6" stroke="#2b2b2b" stroke-width="3"/><circle cx="11" cy="11" r="2" fill="#2b2b2b"/></svg></div>
    <h3>Capable Of Downloading</h3>
    <p>There will be categories of music which would be sorted by the genre. They include RnB, Hip-Hop.</p>
  </div>
</section>

<footer class="site-footer">
  <div class="brand"><span class="brand-dot"></span>Vorde Sound</div>
  <div class="contact-row">
    <div class="contact"><span class="ring"><svg width="16" height="12" viewBox="0 0 16 12"><rect x="1" y="1" width="14" height="10" rx="1.5" fill="none" stroke="#2b2b2b" stroke-width="1.6"/><path d="M1 2l7 5 7-5" fill="none" stroke="#2b2b2b" stroke-width="1.6"/></svg></span>info@vordesound.example</div>
    <div class="contact"><span class="ring"><svg width="15" height="15" viewBox="0 0 16 16"><path d="M3 1l3 3-2 2c1 2.5 3.5 5 6 6l2-2 3 3-2 2C7 15 1 9 1 3z" fill="#2b2b2b"/></svg></span>180 047 3918</div>
  </div>
  <nav class="footer-nav"><span>HOME</span><span>|</span><span>MUSIC</span><span>|</span><span>ARTISTE</span><span>|</span><span>HOTELS</span><span>|</span><span>NEWS</span><span>|</span><span>LOGIN</span></nav>
  <div class="footer-rule"></div>
  <p class="copyright">Copyright © 2017 Vorde Sound. All Right Reserved</p>
  <div class="footer-social" aria-label="Social links">
    <span class="social" style="left:897px"></span>
    <span class="social" style="left:939px"></span>
    <span class="social" style="left:981px"></span>
    <span class="social" style="left:1023px"></span>
    <span class="social" style="left:1064px"></span>
  </div>
</footer>

</body>
</html>
```